Investment company needing business card

We are wanting a business card which looks sharp and easy on the eye. We are thinking of having a business card with the logo embossed on it, to really make it stand out. We will only have a small amount of information of the business card, person's name, position, email address and phone number

Contact Information for Business Card

Danielle Frost
Executive Assistant
+64 21 473 5162
danielf@harwickpartners.co.nz

Requirements
Must have
• Embossed logo
Should not have
• Not to be busy

```html
<!DOCTYPE html>
<html lang="en">
<head>
<meta charset="utf-8">
<title>Harwick Partners – Business Card</title>
<link href="https://fonts.googleapis.com/css2?family=Roboto:wght@400;500&family=Michroma&display=swap" rel="stylesheet">
<style>
  :root{
    --backdrop:#1b1b1c;
    --card:#262627;
    --card-edge:#2e2e30;
    --accent:#22b573;
    --text:#f2f2f2;
    --muted:#d8d8d8;
  }
  *{margin:0;padding:0;box-sizing:border-box}
  html,body{width:1200px;height:900px;overflow:hidden;background:var(--backdrop)}
  .canvas{position:relative;width:1200px;height:900px;display:flex;flex-direction:column;align-items:center;justify-content:center;gap:44px}
  .card{position:relative;width:700px;height:400px;background:linear-gradient(160deg,var(--card-edge),var(--card) 55%);border-bottom:7px solid var(--accent);box-shadow:0 14px 30px rgba(0,0,0,.45);overflow:hidden}
  .brand{display:flex;align-items:center;gap:14px}
  .brand-mark{width:52px;height:52px;background:var(--accent);flex:none}
  .brand-name{font-family:"Michroma",sans-serif;color:var(--accent);line-height:1.15;letter-spacing:.06em}
  .card-front .brand{position:absolute;left:50%;top:50%;transform:translate(-50%,-58%)}
  .card-front .brand-name{font-size:30px}
  .card-front .brand-mark{width:68px;height:68px}
  .card-back .brand{position:absolute;left:48px;top:152px}
  .card-back .brand-name{font-size:18px}
  .divider{position:absolute;left:318px;top:120px;width:2px;height:150px;background:var(--accent)}
  .contact{position:absolute;left:350px;top:128px;font-family:"Roboto",sans-serif;color:var(--text)}
  .contact-name{font-size:34px;font-weight:500;color:var(--accent);letter-spacing:.04em;text-transform:uppercase;line-height:1}
  .contact-role{font-size:17px;color:var(--muted);margin-top:6px}
  .contact-list{list-style:none;margin-top:24px}
  .contact-list li{display:flex;align-items:center;gap:12px;font-size:17px;line-height:1.5}
  .contact-list svg{width:13px;height:13px;flex:none}
</style>
</head>
<body>
<main class="canvas">
  <section class="card card-front">
    <div class="brand">
      <span class="brand-mark"></span>
      <span class="brand-name">HARWICK<br>PARTNERS</span>
    </div>
  </section>

  <section class="card card-back">
    <div class="brand">
      <span class="brand-mark"></span>
      <span class="brand-name">HARWICK<br>PARTNERS</span>
    </div>
    <div class="divider"></div>
    <div class="contact">
      <h1 class="contact-name">Danielle Frost</h1>
      <p class="contact-role">Executive Assistant</p>
      <ul class="contact-list">
        <li>
          <svg viewBox="0 0 16 16" aria-hidden="true"><path d="M4 1l3 3-2 2c1 2 3 4 5 5l2-2 3 3-2 3C7 15 1 9 1 3z" fill="var(--accent)"/></svg>
          +64 21 473 5162
        </li>
        <li>
          <svg viewBox="0 0 16 16" aria-hidden="true"><rect x="1" y="3" width="14" height="10" fill="none" stroke="var(--accent)" stroke-width="1.5"/><path d="M1 3l7 6 7-6" fill="none" stroke="var(--accent)" stroke-width="1.5"/></svg>
          danielf@harwickpartners.co.nz
        </li>
        <li>
          <svg viewBox="0 0 16 16" aria-hidden="true"><circle cx="8" cy="8" r="6.5" fill="none" stroke="var(--accent)" stroke-width="1.5"/><path d="M1.5 8h13M8 1.5c-3 3-3 10 0 13M8 1.5c3 3 3 10 0 13" fill="none" stroke="var(--accent)" stroke-width="1.2"/></svg>
          www.harwickpartners.co.nz
        </li>
      </ul>
    </div>
  </section>
</main>
</body>
</html>
```